Packaged Food Business Needs a Packaging Design

We need a package design to be used as a label/sticker on the lids of round and square transparent plastic containers and on the sides of resealable stand-up pouches. The brand name is 'Savorine' - please find attached logo together with pictures of the sample containers and pouch. We will use the packaging to market a wide variety of food categories from nuts, dried fruits, spices, cooking chocolates, baking ingredients, cereals, grains and pulses.

OVERALL FEEDBACK ON DESIGNS ALREADY RECEIVED:

- We have found so far that a lot of our mandatory requirements are not adhered to in designs that have been submitted so far. We would like to emphasise that the ingredient, weight and expiry text will be printed at the time of packing so it should not take prime space on the pack BUT at the same time some 'blank' space needs to flawlessly be incorporated into the overall design for this purpose
- We encourage you to glorify the brand logo in the pack, and absolutely refrain from duplicating the tagline
- Please note that ONE label design will be used to pack a wide variety of food ingredients and therefore please ensure that the choice of your design incorporates this requirement, in the past we have received designs that are limited to only one type of food (like nuts) or have received designs that are too floral or leafy (and not grounded to food
- Please ensure that you submit designs for all three packaging formats, it is critical to see the family look from the on-set

Target Market(s)

The brand is targeting both mothers and professional chefs and therefore the label design should be broadly approachable and convey affordable premium

Industry/Entity Type

Business

Requirements
Must have
• - Consistent with the brand name and logo, the overall look and feel of the packaging should convey values of healthy, gourmet food ingredients, high in nourishment and project a sense of delightful taste
• - The design styling to be modern and 'simplistic' (embracing 'less-is-more' type of a design style)
• - Design a packaging architecture that incorporates the brand logo together with its tagline lock-up of 'taste the goodness in every spoonful' - find logo attached
• - The design needs to have a dedicated area to print the ingredient (e.g., Mixed Nuts), weight (e.g., 500g) and expiry (this space needs to be flawlessly incorporated into the design) - this information will be printed either with an inkjet printer or with a rubber stamp so please leave an empty space (the text should not be part of the design, just the area for the text needs to be included in the design)
• - The packaging must include 'Packed By: Kestomar Traders Ltd, P. O. Box 51946, Kampala - Uganda'
• - For the design of the resealable pouch, please incorporate a window to see through the ingredients and a hole on top to hang on supermarket pegs if necessary
Nice to have
• - We would love to have some design submissions that are bold and cheerful and fun (but not frivolous) - please see attached inspiration for 'fun' packaging. The attachments are purely for inspiration, not to infringe on anyone else's TM and copyrights
• - Incorporate green to convey healthy, organic values
• - Explore use of gold and silver convey premiumness
Should not have
• - Do not duplicate the tagline
• - Do not include the ingredient, weight and expiry in the main graphic of the design, these will be printed at the time of packing so ensure there is provision for this in a flawless way in the design (e.g., via a blank space allocated for this purpose)

```html
<!DOCTYPE html>
<html lang="en">
<head>
<meta charset="UTF-8">
<title>Savorine Label</title>
<link rel="stylesheet" href="https://fonts.googleapis.com/css2?family=Oswald:wght@600&family=Montserrat:wght@700&family=Roboto:wght@400&display=swap">
<style>
  :root {
    --bg: #efe7e5;
    --green-dark: #4ea83a;
    --green-light: #a6cf3d;
    --label-white: #ffffff;
    --brand-brown: #3f2414;
    --tag-green: #4f9a30;
    --ink: #222222;
  }
  html, body {
    margin: 0;
    padding: 0;
    width: 1200px;
    height: 1200px;
    overflow: hidden;
    background: var(--bg);
  }
  .label {
    position: relative;
    width: 1200px;
    height: 1200px;
  }
  .label-shape {
    position: absolute;
    inset: 0;
  }
  .brand-name {
    position: absolute;
    top: 400px;
    left: 0;
    width: 1200px;
    margin: 0;
    text-align: center;
    font-family: "Oswald", sans-serif;
    font-weight: 600;
    font-size: 150px;
    line-height: 1;
    letter-spacing: 12px;
    color: var(--brand-brown);
  }
  .tagline {
    position: absolute;
    top: 590px;
    left: 0;
    width: 1200px;
    margin: 0;
    text-align: center;
    font-family: "Montserrat", sans-serif;
    font-weight: 700;
    font-size: 24px;
    letter-spacing: 3px;
    text-transform: uppercase;
    color: var(--tag-green);
  }
  .divider {
    position: absolute;
    top: 650px;
    left: 470px;
    width: 260px;
    height: 2px;
    background: var(--tag-green);
    opacity: 0.7;
  }
  .print-area {
    position: absolute;
    top: 670px;
    left: 320px;
    width: 560px;
    height: 220px;
  }
  .packer {
    position: absolute;
    top: 905px;
    left: 0;
    width: 1200px;
    margin: 0;
    text-align: center;
    font-family: "Roboto", sans-serif;
    font-size: 21px;
    line-height: 1.3;
    color: var(--ink);
  }
</style>
</head>
<body>
  <main class="label">
    <svg class="label-shape" width="1200" height="1200" viewBox="0 0 1200 1200" aria-hidden="true">
      <defs>
        <g id="scallop">
          <circle cx="600" cy="600" r="440"/>
          <circle cx="1020" cy="600" r="130"/>
          <circle cx="963.7" cy="810" r="130"/>
          <circle cx="810" cy="963.7" r="130"/>
          <circle cx="600" cy="1020" r="130"/>
          <circle cx="390" cy="963.7" r="130"/>
          <circle cx="236.3" cy="810" r="130"/>
          <circle cx="180" cy="600" r="130"/>
          <circle cx="236.3" cy="390" r="130"/>
          <circle cx="390" cy="236.3" r="130"/>
          <circle cx="600" cy="180" r="130"/>
          <circle cx="810" cy="236.3" r="130"/>
          <circle cx="963.7" cy="390" r="130"/>
        </g>
      </defs>
      <use href="#scallop" fill="var(--green-dark)" transform="translate(600 600) scale(0.98) translate(-600 -600)"/>
      <use href="#scallop" fill="var(--green-light)" transform="translate(600 600) rotate(15) scale(0.92) translate(-600 -600)"/>
      <use href="#scallop" fill="var(--label-white)" transform="translate(600 600) scale(0.83) translate(-600 -600)"/>
      <g class="seal">
        <circle cx="870" cy="330" r="56" fill="var(--label-white)" stroke="var(--green-dark)" stroke-width="5"/>
        <circle cx="870" cy="330" r="44" fill="none" stroke="var(--green-light)" stroke-width="3"/>
      </g>
    </svg>

    <h1 class="brand-name">SAVORINE</h1>
    <p class="tagline">Taste the goodness in every spoonful!</p>
    <div class="divider"></div>
    <div class="print-area"></div>
    <p class="packer">Kestomar Traders Ltd,<br>P. O. Box 51946,<br>Kampala - Uganda</p>
  </main>
</body>
</html>
```